Upstart Retirement Planning Firm needs help with business card design

Harborview Nest Advisors, LLC is looking for help with business card design. We give advice on investments, insurance, and other financial matters related to retirement. There are some required disclosures that we will provide but mostly we are looking for a professional, classy business card that reflects the theme we have chosen. We have a logo that is attached but we would like to add a phrase; "Turning Your Earned Income Into Retirement Income"

Doubled sided only so that we can add the required disclosures (needed for our industry) on the back of the card. We will provide the exact words for this in 1-2 days.

Target Market(s)

Retirees and Pre-retirees. Professionals 50+ years old

Industry/Entity Type

Financial Planning

Contact Information for Business Card

We currently have two people who will need separate cards so we'd like to have a template so that we can add names for new cards in the future.

For the first run, please show the following information.

Gregor Pelham, MBA, ChFC®, CLU®
Financial Advisor, Registered Representative
gpelham@harborviewnest.example
Phone: (555) 318-2946
Toll Free Fax: (800) 555-0193

Address is
2187 Meadowlark Ridge Rd.
Suite K418
Virginia Beach, VA 23999

Colors
3277b5

Requirements
Must have
• Logo, contact info, small phase to describe business (in description), required legal disclosures on back of the card as follows (in small font)
• Gregor Pelham is a registered representative of and offers securities through Brightmoor Capital Brokerage Corporation, Member FNQX. Brightmoor Capital Brokerage Corporation is a member of the Brightmoor Capital Alliance which is the marketing name for Brightmoor Holding Corporation and its affiliates.
Nice to have
• Rounded edges, raised letters
Should not have
• any colors that aren't in the logo (other than black for font)

```html
<!DOCTYPE html>
<html lang="en">
<head>
<meta charset="utf-8">
<title>Harborview Nest Advisors, LLC – Business Card</title>
<link rel="stylesheet" href="https://fonts.googleapis.com/css2?family=Open+Sans:wght@400;600;700&display=swap">
<style>
  :root {
    --backdrop: #2b2b2d;
    --card: #141416;
    --card-edge: #1f1f22;
    --brand-blue: #3277b5;
    --silver: #b9bcc0;
    --text: #ecedef;
  }
  * { box-sizing: border-box; margin: 0; padding: 0; }
  html, body { width: 1200px; height: 900px; overflow: hidden; }
  body {
    background: var(--backdrop);
    font-family: "Open Sans", Arial, sans-serif;
    color: var(--text);
    position: relative;
  }
  .card {
    position: absolute;
    top: 295px;
    width: 530px;
    height: 310px;
    background: var(--card);
    border: 1px solid var(--card-edge);
    border-radius: 22px;
  }
  .card--contact { left: 45px; }
  .card--brand { left: 625px; }

  /* Contact side */
  .brand-mark {
    position: absolute;
    left: 34px;
    top: 40px;
    display: flex;
    align-items: center;
    gap: 10px;
    width: 180px;
  }
  .brand-mark__dot {
    flex: none;
    width: 14px; height: 14px;
    border-radius: 50%;
    background: var(--brand-blue);
  }
  .brand-mark__name {
    font-size: 17px;
    font-weight: 600;
    line-height: 1.2;
    color: var(--brand-blue);
  }
  .contact {
    position: absolute;
    left: 232px;
    top: 40px;
    right: 20px;
  }
  .contact__name {
    font-size: 17px;
    font-weight: 600;
    color: var(--brand-blue);
    white-space: nowrap;
  }
  .contact__name .credentials { font-size: 11px; font-weight: 400; }
  .contact__title { font-size: 13px; margin-top: 2px; }
  .contact__list { list-style: none; margin-top: 14px; font-size: 13px; }
  .contact__list li { display: flex; align-items: center; gap: 7px; margin-bottom: 4px; white-space: nowrap; }
  .contact__list svg { width: 11px; height: 11px; fill: var(--brand-blue); flex: none; }
  .contact__fax { font-size: 13px; margin-top: 2px; white-space: nowrap; }
  .contact__fax-label { color: var(--brand-blue); font-weight: 600; }
  .contact__fax-number { font-weight: 700; }
  .contact__address { font-size: 13px; margin-top: 16px; line-height: 1.45; }

  /* Brand side */
  .brand-side {
    position: absolute;
    inset: 0;
    display: flex;
    flex-direction: column;
    align-items: center;
    justify-content: center;
  }
  .brand-side__mark { display: flex; align-items: center; gap: 12px; }
  .brand-side__dot { width: 18px; height: 18px; border-radius: 50%; background: var(--brand-blue); }
  .brand-side__name { font-size: 26px; font-weight: 600; color: var(--silver); }
  .brand-side__rule { width: 300px; height: 1px; background: var(--silver); margin: 16px 0 14px; opacity: .7; }
  .brand-side__tagline { font-size: 15px; font-weight: 700; color: var(--text); }
</style>
</head>
<body>
  <section class="card card--contact">
    <div class="brand-mark">
      <span class="brand-mark__dot"></span>
      <span class="brand-mark__name">Harborview Nest Advisors, LLC</span>
    </div>
    <div class="contact">
      <p class="contact__name">Gregor Pelham, MBA, <span class="credentials">ChFC®, CLU®</span></p>
      <p class="contact__title">Financial Advisor, Registered Representative</p>
      <ul class="contact__list">
        <li>
          <svg viewBox="0 0 24 24" aria-hidden="true"><path d="M6.6 10.8a15.1 15.1 0 0 0 6.6 6.6l2.2-2.2a1 1 0 0 1 1-.25 11.4 11.4 0 0 0 3.6.57 1 1 0 0 1 1 1V20a1 1 0 0 1-1 1A17 17 0 0 1 3 4a1 1 0 0 1 1-1h3.5a1 1 0 0 1 1 1c0 1.25.2 2.45.57 3.57a1 1 0 0 1-.25 1z"/></svg>
          (555) 318-2946
        </li>
        <li>
          <svg viewBox="0 0 24 24" aria-hidden="true"><path d="M2 5h20v14H2z M2 5l10 8 10-8" fill="none" stroke="#3277b5" stroke-width="2"/><path d="M2 6l10 7 10-7v13H2z"/></svg>
          gpelham@harborviewnest.example
        </li>
      </ul>
      <p class="contact__fax"><span class="contact__fax-label">TOLL FREE FAX:</span> <span class="contact__fax-number">(800) 555-0193</span></p>
      <p class="contact__address">2187 Meadowlark Ridge Rd. Suite<br>K418 Virginia Beach, VA 23999</p>
    </div>
  </section>

  <section class="card card--brand">
    <div class="brand-side">
      <div class="brand-side__mark">
        <span class="brand-side__dot"></span>
        <span class="brand-side__name">Harborview Nest Advisors, LLC</span>
      </div>
      <div class="brand-side__rule"></div>
      <p class="brand-side__tagline">Turning Your Earned Income Into Retirement Income</p>
    </div>
  </section>
</body>
</html>
```